Flyer for Yoga and IronPulse.

Just initial idea and open to creativity: I am thinking right half of flyer to be IronPulse info and left half to be Yoga info.
Feel free to add text as needed but would like following:
Basic text: ZenLoftVo $69/mo unlimited sessions.
ZenLoftVO.com
IronPulse: $99 intro session. Largest IronPulse in Texas.
IronPulseVO.com

Located North Riverside Houston (NRVO)
Address: 4817 Marlow Pkwy Houston, tx

Please submit any and all designs. Looking to get some great ideas!

Target Market(s)

Young professionals free spirited and fun atmosphere.

Colors
3176b5
85acd3
32a6d7
32b7a4
f59195
cde9f5
f04a50

Requirements
Must have
• Professional yet fun. Text should include:
ZenLoftVo and IronPulse Vo taking each a half of the page seperatly get still be identifiable as one. Want to show there is two options for either yoga or IronPulse or do both!
IronPulse Intro is $99 adm yoga intro is $69.
Nice to have
• Also visit www.ironpulsevo.com for more ideas and info.

```html
<!DOCTYPE html>
<html lang="en">
<head>
<meta charset="utf-8">
<title>ZenLoftVo &amp; IronPulse Vo Flyer</title>
<link href="https://fonts.googleapis.com/css2?family=Bree+Serif&family=Montserrat:wght@600&display=swap" rel="stylesheet">
<style>
  :root {
    --yoga-blue: #2b78b8;
    --yoga-blue-soft: #6aa3d6;
    --pulse-red: #f04a50;
    --pulse-red-soft: #f7888b;
    --pulse-dark-red: #c0272d;
    --yoga-rose: #d24a5c;
    --yoga-teal: #32b7c4;
    --ink: #222222;
    --grey: #555555;
    --rule: #9a9a9a;
    --white: #ffffff;
  }
  * { margin: 0; padding: 0; box-sizing: border-box; }
  html, body { width: 883px; height: 1200px; overflow: hidden; background: var(--white); }
  .flyer {
    position: relative; width: 883px; height: 1200px; overflow: hidden;
    font-family: "Bree Serif", Georgia, serif; color: var(--white);
  }
  .flyer-bg { position: absolute; inset: 0; }
  .text { position: absolute; text-align: center; line-height: 1; white-space: nowrap; }
  .yoga-col { left: 0; width: 440px; }
  .pulse-col { left: 440px; width: 443px; }

  .yoga-url { top: 68px; font-size: 34px; }
  .yoga-price { top: 146px; font-size: 58px; }
  .yoga-note { top: 206px; font-size: 35px; }

  .art { position: absolute; }
  .yoga-art {
    left: 30px; top: 330px; width: 400px; height: 370px;
    background: radial-gradient(ellipse at 50% 50%, var(--yoga-blue-soft) 0%, rgba(106,163,214,0.45) 45%, rgba(43,120,184,0) 72%);
  }
  .pulse-art {
    left: 500px; top: 425px; width: 330px; height: 430px;
    background: radial-gradient(ellipse at 50% 50%, var(--pulse-red-soft) 0%, rgba(247,136,139,0.45) 45%, rgba(240,74,80,0) 72%);
  }

  .brand-mark { position: absolute; border-radius: 50%; }
  .yoga-mark { left: 202px; top: 752px; width: 36px; height: 36px; background: var(--yoga-teal); }
  .rule { position: absolute; height: 1px; background: var(--rule); }
  .yoga-name { font-size: 88px; color: var(--yoga-rose); }
  .yoga-name-top { top: 806px; }
  .yoga-name-bottom { top: 898px; }

  .pulse-name { top: 150px; font-size: 72px; color: var(--pulse-dark-red); }
  .pulse-claim { top: 252px; font-size: 32px; color: var(--ink); }
  .place {
    position: absolute; text-align: center; font-family: "Montserrat", Arial, sans-serif;
    font-weight: 600; font-size: 11px; letter-spacing: 2px; color: var(--grey);
  }

  .pulse-price { top: 893px; font-size: 64px; }
  .pulse-note { top: 962px; font-size: 38px; }
  .pulse-url { top: 1030px; font-size: 38px; }

  .footer {
    position: absolute; left: 0; top: 1121px; width: 883px; height: 79px;
    display: flex; align-items: center; justify-content: center; gap: 12px;
    color: var(--ink); font-size: 24px;
  }
  .pin { width: 20px; height: 28px; }
</style>
</head>
<body>
<main class="flyer">
  <svg class="flyer-bg" width="883" height="1200" viewBox="0 0 883 1200" aria-hidden="true">
    <rect x="0" y="0" width="440" height="1121" fill="var(--yoga-blue)"/>
    <polygon points="0,739 220,697 440,739 440,1097 220,1055 0,1097" fill="var(--white)"/>
    <rect x="440" y="0" width="443" height="1121" fill="var(--pulse-red)"/>
    <polygon points="440,22 661,66 883,22 883,363 661,416 440,363" fill="var(--white)"/>
    <rect x="0" y="1121" width="883" height="79" fill="var(--white)"/>
  </svg>

  <section class="yoga">
    <p class="text yoga-col yoga-url">ZenLoftVO.com</p>
    <p class="text yoga-col yoga-price">$69/month</p>
    <p class="text yoga-col yoga-note">unlimited sessions</p>
    <div class="art yoga-art" role="img" aria-label="White silhouette of a woman in a side-stretch yoga pose"></div>
    <span class="brand-mark yoga-mark"></span>
    <span class="rule" style="left:100px; top:796px; width:240px;"></span>
    <p class="text yoga-col yoga-name yoga-name-top">ZenLoft</p>
    <p class="text yoga-col yoga-name yoga-name-bottom">Vo</p>
    <span class="rule" style="left:100px; top:990px; width:240px;"></span>
    <p class="place" style="left:0; width:440px; top:999px;">NORTH RIVERSIDE HOUSTON</p>
  </section>

  <section class="pulse">
    <p class="text pulse-col pulse-name">IronPulse Vo</p>
    <p class="text pulse-col pulse-claim">Largest IronPulse in Texas</p>
    <span class="rule" style="left:540px; top:312px; width:243px;"></span>
    <p class="place" style="left:440px; width:443px; top:321px;">NORTH RIVERSIDE HOUSTON</p>
    <div class="art pulse-art" role="img" aria-label="White silhouette of an athlete lifting a barbell overhead in a split stance"></div>
    <p class="text pulse-col pulse-price">$99</p>
    <p class="text pulse-col pulse-note">intro session</p>
    <p class="text pulse-col pulse-url">IronPulseVO.com</p>
  </section>

  <footer class="footer">
    <svg class="pin" viewBox="0 0 20 28" aria-hidden="true">
      <path d="M10 0C4.5 0 0 4.4 0 9.8 0 17 10 28 10 28s10-11 10-18.2C20 4.4 15.5 0 10 0zm0 14a4.2 4.2 0 1 1 0-8.4 4.2 4.2 0 0 1 0 8.4z" fill="var(--ink)"/>
    </svg>
    <span>4817 Marlow Pkwy Houston, North Riverside Houston (NRVO), Texas</span>
  </footer>
</main>
</body>
</html>
```